Brochure for a civil enineering company in A4 format

I need a brochure design for our company TIRO Engineering S.r.l.. We are an engineering consultant company. Our main clients are from the infrastructure industry (geotechnical and underground sectors mainly).
We are looking for a 2 pages (4 faces) fold out design with a glued pocket where we can put individual data sheets.
I need A4 format pages.

Target Market(s)

We are an engineering consultant company. Our main clients are from the infrastructure industry (geotechnical and underground sectors mainly).

Industry/Entity Type

Civil Engineer

Font styles to use
Sans Serif

Requirements
Must have
• Overall: 2 pages in A4 format
Essential style. Bright and modern appearance.
Glued pocket
Logo integrated in a picture on the pocket where I would like to insert a slogan (… tiro engineering … reliable solutions …)
Attached are selected images which the designer can use and edit at their own discretion.
Some advice in the following (anyway designers are free to provide their solutions):
Outer sheets:
Front page with name, logo. It could be nice to have the “m” of the logo integrated in a pictures, also a modified picture (I mean modify one of the attached pictures) so to create a general image and do not tie the cover to a specific job.
Back page: offices address and contact email address. Nice to have one space for a slogan.
Inner sheet: text that I upload in the file “inside-sheets”, possibly with pictures on each sheet. In the right faces insert the glued pocket. On this pages insert the section OUR EXPERIENCE ….with a space for a picture of our team.
Nice to have
• Clean and essential design.
Pictures choosing from the atteched ones. Pictures could be modified in a very light manner to make them a general idea of the work ( I mean geotechnical world) without to be immediately linked to a specific site.
Should not have
• excessive frills

```html
<!DOCTYPE html>
<html lang="it">
<head>
<meta charset="utf-8">
<title>TIRO Engineering – Brochure</title>
<link href="https://fonts.googleapis.com/css2?family=Montserrat:wght@600;700&family=Open+Sans:wght@400;600;700&display=swap" rel="stylesheet">
<style>
  :root{
    --stage:#ececec;
    --paper:#ffffff;
    --ink:#111111;
    --black:#0a0a0a;
    --grey:#8a8a8a;
    --light:#d9d9d9;
    --white:#ffffff;
  }
  *{margin:0;padding:0;box-sizing:border-box}
  html,body{width:900px;height:1200px;overflow:hidden;background:var(--stage)}
  body{position:relative;font-family:"Open Sans",Arial,sans-serif;color:var(--ink)}
  .spread{position:absolute;left:88px;width:734px;height:517px;display:flex}
  .spread--outer{top:57px}
  .spread--inner{top:617px}
  .page{position:relative;width:367px;height:100%;overflow:hidden}
  .page--white{background:var(--paper)}
  .page--black{background:var(--black);color:var(--white)}

  .heading{font-family:"Montserrat",Arial,sans-serif;font-weight:700;letter-spacing:.3px}
  .body-text{font-size:6.4px;line-height:8.3px;text-align:justify}
  .body-text p+p{margin-top:8px}

  .brand{position:absolute;text-align:center;font-family:"Open Sans",Arial,sans-serif}
  .brand__name{font-weight:700;line-height:1;letter-spacing:1px}
  .brand__tag{font-size:5.2px;letter-spacing:1.6px;text-transform:uppercase;margin-top:3px}
  .website{position:absolute;font-size:8.5px;letter-spacing:3.4px}

  /* Back cover */
  .company__title{position:absolute;top:48px;left:0;width:100%;text-align:center;font-size:15px}
  .company__text{position:absolute;top:72px;left:40px;width:291px}
  .site-photo{position:absolute;left:0;right:0;top:232px;bottom:0;background:linear-gradient(180deg,rgba(255,255,255,1) 0%,#e6e6e6 25%,#d4d4d4 60%,#eeeeee 100%)}
  .office{position:absolute;left:72px;width:223px;height:64px;background:var(--black);color:var(--white);border:1px solid #555;border-radius:3px;text-align:center;padding-top:6px}
  .office__name{font-family:"Montserrat",Arial,sans-serif;font-weight:700;font-size:10.5px;margin-bottom:3px}
  .office__line{font-size:6.8px;line-height:8.2px}
  .office__line b{font-weight:700}

  /* Front cover */
  .tunnel-photo{position:absolute;left:0;top:0;width:100%;height:420px;background:radial-gradient(ellipse at 70% 52%,#d8d0c0 0%,#7a7064 10%,#3b342e 28%,#1b1715 55%,#0a0a0a 80%)}

  /* Inner left */
  .expertise{position:absolute;left:0;top:0;width:217px;height:100%;background:var(--black);color:var(--white)}
  .expertise__title{position:absolute;left:18px;top:28px;font-size:15px;line-height:17px}
  .expertise__text{position:absolute;left:18px;top:73px;width:185px;height:340px;overflow:hidden;font-size:6.2px;line-height:8px}
  .work-photo{position:absolute;left:209px;width:111px;border:2px solid var(--white);box-shadow:0 0 0 1px #999}

  /* Inner right */
  .services__title{position:absolute;left:101px;top:5px;width:160px;height:35px;background:var(--black);color:var(--white);font-size:14px;display:flex;align-items:center;justify-content:center}
  .services__text{position:absolute;left:17px;top:53px;width:333px;height:336px;overflow:hidden;font-size:6.1px;line-height:7.9px}
  .services__text p+p{margin-top:0}
  .pocket{position:absolute;left:17px;top:393px;width:333px;height:110px;background:var(--black);color:var(--white);padding:8px 10px}
  .pocket__lead{font-size:6.3px;line-height:8px;margin-bottom:8px}
  .pocket__cols{display:flex;gap:8px}
  .pocket__col{flex:1;font-size:6.3px;line-height:8px}
  .pocket__col--boxed{background:#1c1c1c;padding:2px 3px}
</style>
</head>
<body>

<!-- Outer sheet: back and front cover -->
<section class="spread spread--outer">
  <article class="page page--white back-cover">
    <h2 class="heading company__title">OUR COMPANY</h2>
    <div class="body-text company__text">
      <p>TIRO Engineering S.r.l. offre servizi di consulenza tecnica, contrattuale e strategica ai principali attori nei settori delle scienze geologiche, dell'ingegneria geotecnica e dell'ingegneria idraulica. Lavoriamo per mitigare il rischio e ridurre l'incertezza, con flessibilità nella ricerca della soluzione ottimale contribuendo ad aumentare la redditività del progetto.</p>
      <p>TIRO Engineering S.r.l. è una società indipendente che nasce nel luglio 2020 dall'associazione di un gruppo di professionisti che hanno messo a fattor comune la reciproca esperienza maturata in oltre trent'anni di attività come progettisti e consulenti nel settore delle grandi opere di ingegneria civile lavorando come Direttori Tecnici di Main Engineering Companies and as Freelancers.</p>
      <p>TIRO Engineering S.r.l. vuole unire l'esperienza dei Fondatori e delle figure chiave con l'entusiasmo di chi intraprende una nuova attività, per dare vita ad una nuova realtà che si pone come obbiettivo principale il design of infrastructures that are safe, sustainable and economic.<br>Each of our projects represents a long term commitment, we believe in providing safe, reliable, sustainable and innovative solutions. This is and will be our distinctive characteristic.</p>
    </div>
    <div class="site-photo" role="img" aria-label="Faded black and white view of a construction site"></div>
    <div class="brand" style="left:0;width:100%;top:238px;color:var(--ink)">
      <div class="brand__name" style="font-size:30px">tiro</div>
      <div class="brand__tag">tiro engineering . reliable solutions</div>
    </div>
    <div class="office" style="top:297px">
      <div class="office__name">VIA FERRI, 14</div>
      <div class="office__line">20121 Milano - IT</div>
      <div class="office__line"><b>T: +39 02 5550148</b></div>
      <div class="office__line">E: tiro_info@tiroengineering.org</div>
    </div>
    <div class="office" style="top:367px">
      <div class="office__name">ARCO TN</div>
      <div class="office__line">Via S. Marco, 9</div>
      <div class="office__line">38062 Arco TN - IT</div>
      <div class="office__line"><b>T: +39 02 5550148</b></div>
      <div class="office__line">E: tiro_info@tiroengineering.org</div>
    </div>
    <div class="website" style="left:0;width:100%;text-align:center;top:476px">www.tiroengineering.org</div>
  </article>

  <article class="page page--black front-cover">
    <div class="tunnel-photo" role="img" aria-label="Dark tunnel under construction with lit steel arch ribs and a worker in the distance"></div>
    <div class="brand" style="left:0;width:100%;top:404px;color:var(--white)">
      <div class="brand__name" style="font-size:54px">tiro</div>
      <div class="brand__tag" style="font-size:6.4px;letter-spacing:2px">tiro engineering . reliable solutions</div>
    </div>
    <div class="website" style="left:0;width:100%;text-align:center;top:476px;color:var(--white)">www.tiroengineering.org</div>
  </article>
</section>

<!-- Inner sheet: expertise and services -->
<section class="spread spread--inner">
  <article class="page page--white expertise-page">
    <div class="expertise">
      <h2 class="heading expertise__title">OUR EXPERTISE AND<br>EXPERIENCE</h2>
      <div class="body-text expertise__text">
        <p>Progettazione e consulenza specialistica nel campo della geologia, dell'ingegneria geotecnica, delle opere sotterranee e dell'ingegneria idraulica.<br>Aiutiamo i nostri clienti a risolvere problemi di natura progettuale, contrattuale e costruttiva che possono nascere nell'intera vita del progetto portando la nostra esperienza all'interno delle loro organizzazioni, migliorando la qualità dei loro servizi di ingegneria, ottimizzando i loro progetti, proponendo nuove idee e soluzioni, rafforzando i loro approcci ……<br>TIRO Engineering è in grado di fornire la propria assistenza nell'intero iter procedurale, dalla fase di indagine preliminare e di analisi di fattibilità fino alla progettazione costruttiva e all'assistenza tecnica in fase realizzativa.<br>La specializzazione e l'esperienza accumulate nelle discipline della geologia, dell'ingegneria geotecnica e del sottosuolo e dell'idraulica ci permette di massimizzare la nostra efficacia quando sia necessario:</p>
        <p>Progettazione e consulenza specialistica nel campo della geologia, dell'ingegneria geotecnica, delle opere sotterranee e dell'ingegneria idraulica.<br>Aiutiamo i nostri clienti a risolvere problemi di natura progettuale, contrattuale e costruttiva che possono nascere nell'intera vita del progetto portando la nostra esperienza all'interno delle loro organizzazioni, migliorando la qualità dei loro servizi di ingegneria, ottimizzando i loro progetti, proponendo nuove idee e soluzioni, rafforzando i loro approcci ……<br>TIRO Engineering è in grado di fornire la propria assistenza nell'intero iter procedurale, dalla fase di indagine preliminare e di analisi di fattibilità fino alla progettazione costruttiva e all'assistenza tecnica in fase realizzativa.<br>La specializzazione e l'esperienza accumulate nelle discipline della geologia, dell'ingegneria geotecnica e del sottosuolo e dell'idraulica ci permette di massimizzare la nostra efficacia quando sia necessario:</p>
      </div>
      <div class="website" style="left:18px;top:486px;font-size:7.6px;letter-spacing:2.2px">www.tiroengineering.org</div>
    </div>
    <div class="work-photo" style="top:45px;height:103px;background:linear-gradient(160deg,#4d5a5e,#2a3336 55%,#8b7a3a)" role="img" aria-label="Shaft excavation seen from above with drilling rig"></div>
    <div class="work-photo" style="top:158px;height:118px;background:linear-gradient(180deg,#3d4a60,#24324a 55%,#5a6c86)" role="img" aria-label="Twin tunnel portals with lit interiors"></div>
    <div class="work-photo" style="top:286px;height:109px;background:linear-gradient(170deg,#7d8b6c,#9a9684 45%,#6c7458)" role="img" aria-label="Aerial view of a construction yard with a large shed"></div>
    <div class="brand" style="left:235px;width:110px;top:455px;color:var(--ink)">
      <div class="brand__name" style="font-size:24px">tiro</div>
      <div class="brand__tag" style="font-size:4.4px;letter-spacing:1.2px">tiro engineering . reliable solutions</div>
    </div>
  </article>

  <article class="page page--white services-page">
    <h2 class="heading services__title">OUR SERVICES</h2>
    <div class="body-text services__text">
      <p>La società nasce dall'associazione di un gruppo di professionisti, con indiscusse competenze ed affidabilità, con esperienza maturata in oltre trent'anni di attività come progettisti e consulenti nel settore delle grandi opere di ingegneria civile; geologia, ingegneria geotecnica ed idraulica ed opere sotterranee sono il "core" delle loro competenze ….<br>I soci fondatori sono:</p>
      <p>Paolo. Già Direttore Tecnico e Socio di LORVA Srl, nel periodo di sua permanenza fino al dicembre 2018, ha per essa firmato tutti i progetti nel campo delle opere sotterranee e la maggior parte di quelli di ingegneria geotecnica. Da gennaio 2019 è Direttore Tecnico di GEDRA. Può vantare più di 150 gallerie naturali, e numerosi progetti ed assistenze tecniche nel campo delle strutture geotecniche, delle sistemazioni idrogeologiche e dei versanti e delle opere di protezione ambientale. Negli ultimi dieci anni è stato responsabile di attività di assistenza tecnica, per imprese di costruzione, di opere il cui valore supera i 440 Mio EUR e di servizi di progettazione definitiva e/o esecutiva per opere il cui valore supera i 1.400 Mio EUR. Ha svolto attività di verifica e validazione, in Italia ed all'estero, di numerosi progetti il cui valore complessivo supera i 3.400 Mio EUR.</p>
      <p>Guido 30 anni di esperienza professionale. Coinvolto in più di 150 gallerie naturali con lunghezza complessiva superiore a 360 km. Numerosi progetti ed attività di assistenza tecnica nel campo delle strutture, delle sistemazioni idrogeologiche e dei versanti e delle opere di protezione ambientale. Negli ultimi dieci anni responsabile di attività di assistenza tecnica in corso d'opera, per imprese di costruzione, di opere il cui valore supera i 440 Mio EUR e di servizi di progettazione definitiva o esecutiva per opere il cui valore supera i 1.400 Mio EUR. Ha svolto attività di verifica ai fini della validazione, in Italia ed all'estero, di numerosi progetti il cui valore complessivo supera i 3.400 Mio EUR.</p>
      <p>Serena 30 anni di esperienza professionale. Coinvolto in più di 150 gallerie naturali con lunghezza complessiva superiore a 360 km. Numerosi progetti ed attività di assistenza tecnica nel campo delle strutture, delle sistemazioni idrogeologiche e dei versanti e delle opere di protezione ambientale. Negli ultimi dieci anni responsabile di attività di assistenza tecnica in corso d'opera, per imprese di costruzione, di opere il cui valore supera i 440 Mio EUR e di servizi di progettazione definitiva o esecutiva per opere il cui valore supera i 1.400 Mio EUR. Ha svolto attività di verifica ai fini della validazione, in Italia ed all'estero, di numerosi progetti il cui valore complessivo supera i 3.400 Mio EUR.</p>
      <p>Lucia 30 anni di esperienza professionale. Coinvolto in più di 150 gallerie naturali con lunghezza complessiva superiore a 360 km. Numerosi progetti ed attività di assistenza tecnica nel campo delle strutture, delle sistemazioni idrogeologiche e dei versanti e delle opere di protezione ambientale. Negli ultimi dieci anni responsabile di attività di assistenza tecnica in corso d'opera, per imprese di costruzione, di opere il cui valore supera i 440 Mio EUR e di servizi di progettazione definitiva o esecutiva per opere il cui valore supera i 1.400 Mio EUR. Ha svolto attività di verifica ai fini della validazione, in Italia ed all'estero, di numerosi progetti il cui valore complessivo supera i 3.400 Mio EUR.</p>
    </div>
    <div class="pocket">
      <p class="pocket__lead">ottimizzare i progetti redatti da terzi implementandone il contenuto e massimizzando l'efficacia economica degli investimenti.</p>
      <div class="pocket__cols">
        <p class="pocket__col">far fronte a situazioni di emergenza anche su progetti in fase di sviluppo avanzato garantendo l'immediata focalizzazione delle problematiche di progetto e garantendo il risultato finale atteso (in termini di qualità, tempistiche e costi…)</p>
        <p class="pocket__col pocket__col--boxed">fornire "second opinion" di elevato valore tecnico ed amministrativo in occasione di problematiche progettuali e costruttive e dispute legali</p>
        <p class="pocket__col">analizzare in tempi brevi progetti svolti da terzi individuandone le "criticità", verificandone la cantierabilità e la validità tecnico economica.</p>
      </div>
    </div>
  </article>
</section>

</body>
</html>
```